Business card, Stationery and form for Tessel Brook
Tessel Brook, LLC an Energy Broker
Professional
Ilias Montrevet
Principal
47 Ambervale Court
Lakewood, NJ 09314
(555) 014-TESS (8377)
imontrevet@tesselbrook.com
www.tesselbrook.com
I will need to be able to change names etc on them for other workers.
Attached you will find a form that we use regularly (see the comment for the file).
I would also need the stationary designed in a way that is easy to use for word processing in MS Word, such as a template or in a word document that I can type on, besides in any way that may be printed.
I am guessing to use the secondary logo for the back but this is not required. An idea that I had but am unsure how it would look is to make that logo larger and then to place the words inside the lower grey area.
I may choose a full color design with pictures besides the more traditional one which I prefer in order to give the sales force a choice.
This is our primary logo
This is our secondary logo
This is a form which we use regularly. We primarily use the excel version here: http://tesselbrook.com/wp-content/uploads/2012/03/Tessel-Brook-LOA-Form-unprotected.xlsx The form gets minor edits from time to time and I would prefer to have it designed as a header and footer or a template.

```html
<!DOCTYPE html>
<html lang="en">
<head>
<meta charset="utf-8">
<title>Tessel Brook Stationery Concepts</title>
<link href="https://fonts.googleapis.com/css2?family=Open+Sans:wght@400;600;700&display=swap" rel="stylesheet">
<style>
  :root {
    --board: #3b3b3d;
    --board-dark: #2a2a2c;
    --paper: #ffffff;
    --brand-blue: #1d8fc6;
    --brand-cyan: #3fb8e3;
    --brand-navy: #0c4c78;
    --ink: #2d3a45;
    --muted: #7d8a94;
    --label: #b9bcc0;
    --night: #111214;
  }
  * { box-sizing: border-box; margin: 0; padding: 0; }
  html, body { width: 1200px; height: 439px; overflow: hidden; }
  body {
    position: relative;
    background: radial-gradient(ellipse at 50% 40%, var(--board), var(--board-dark));
    font-family: "Open Sans", Arial, sans-serif;
    color: var(--ink);
  }
  .board-title { position: absolute; left: 19px; top: 16px; font-size: 9px; color: var(--label); }
  .item-label { position: absolute; font-size: 6px; color: var(--label); text-align: center; }
  .sheet { position: absolute; background: var(--paper); overflow: hidden; box-shadow: 0 2px 6px rgba(0,0,0,.5); }
  .sheet svg.art { position: absolute; left: 0; top: 0; }
  .wordmark { position: absolute; display: flex; align-items: center; gap: 4px; font-weight: 700; color: var(--brand-navy); white-space: nowrap; }
  .wordmark .dot { border-radius: 50%; background: var(--brand-blue); }
  .wordmark.light { color: var(--paper); }
  .tagline { position: absolute; font-size: 4px; color: var(--muted); }
  .contact { position: absolute; font-size: 4.2px; line-height: 1.45; color: var(--paper); text-align: right; }
  .contact.dark { color: var(--ink); text-align: center; }
  .watermark { position: absolute; border-radius: 50% 50% 48% 48%; background: radial-gradient(ellipse at 45% 55%, rgba(63,184,227,.16), rgba(63,184,227,.03) 70%, transparent); }
</style>
</head>
<body>
  <div class="board-title">Stationery Concepts</div>

  <!-- Business card front -->
  <section class="sheet card card-front" style="left:19px;top:77px;width:101px;height:70px;">
    <svg class="art" width="101" height="70" viewBox="0 0 101 70">
      <path d="M0,52 C30,44 65,50 101,38 V70 H0Z" fill="var(--brand-blue)"/>
      <path d="M0,56 C35,49 70,54 101,44" fill="none" stroke="var(--brand-cyan)" stroke-width="1.2"/>
    </svg>
    <div class="wordmark" style="left:6px;top:9px;font-size:6px;"><span class="dot" style="width:6px;height:6px;"></span>Tessel Brook</div>
    <div class="tagline" style="left:16px;top:18px;">an Energy Broker</div>
    <div class="contact" style="right:5px;top:14px;color:var(--ink);font-size:3.8px;">
      <strong>Ilias Montrevet</strong><br>Principal<br>47 Ambervale Court<br>Lakewood, NJ 09314<br>(555) 014-TESS (8377)<br>imontrevet@tesselbrook.com
    </div>
  </section>
  <div class="item-label" style="left:19px;top:152px;width:101px;">Front Card</div>

  <!-- Business card back option 1 -->
  <section class="sheet card card-back-light" style="left:19px;top:180px;width:101px;height:70px;">
    <svg class="art" width="101" height="70" viewBox="0 0 101 70">
      <path d="M0,60 C35,54 70,58 101,52 V70 H0Z" fill="var(--brand-blue)"/>
    </svg>
    <div class="wordmark" style="left:14px;top:26px;font-size:9px;"><span class="dot" style="width:8px;height:8px;"></span>Tessel Brook</div>
    <div class="tagline" style="left:30px;top:42px;">www.tesselbrook.com</div>
  </section>
  <div class="item-label" style="left:19px;top:255px;width:101px;">Back Card Option 1</div>

  <!-- Business card back option 2 -->
  <section class="sheet card card-back-blue" style="left:19px;top:281px;width:101px;height:70px;background:linear-gradient(160deg,var(--brand-cyan),var(--brand-blue) 55%,var(--brand-navy));">
    <div class="wordmark light" style="left:14px;top:28px;font-size:9px;"><span class="dot" style="width:8px;height:8px;background:var(--paper);"></span>Tessel Brook</div>
  </section>
  <div class="item-label" style="left:19px;top:356px;width:101px;">Back Card Option 2</div>

  <!-- Letterhead option 1 -->
  <section class="sheet letterhead" style="left:137px;top:22px;width:270px;height:380px;">
    <svg class="art" width="270" height="380" viewBox="0 0 270 380">
      <defs>
        <linearGradient id="lhBand" x1="0" y1="0" x2="1" y2="1">
          <stop offset="0" stop-color="var(--brand-cyan)"/><stop offset="1" stop-color="var(--brand-navy)"/>
        </linearGradient>
      </defs>
      <path d="M80,0 H270 V58 C210,32 150,14 80,0Z" fill="url(#lhBand)"/>
      <path d="M0,30 C90,22 180,40 270,66" fill="none" stroke="var(--brand-navy)" stroke-width="2"/>
      <path d="M0,352 C90,338 180,346 270,326 V380 H0Z" fill="url(#lhBand)"/>
    </svg>
    <div class="wordmark" style="left:10px;top:10px;font-size:9px;"><span class="dot" style="width:9px;height:9px;"></span>Tessel Brook</div>
    <div class="tagline" style="left:23px;top:24px;">an Energy Broker</div>
    <div class="contact" style="right:10px;top:8px;">47 Ambervale Court<br>Lakewood, NJ 09314<br>(555) 014-TESS (8377)<br>www.tesselbrook.com</div>
    <div class="watermark" role="img" aria-label="Faint enlarged brand emblem" style="left:50px;top:90px;width:170px;height:230px;"></div>
  </section>
  <div class="item-label" style="left:137px;top:408px;width:270px;">Letterhead Option 1</div>

  <!-- Letterhead option 2 -->
  <section class="sheet letterhead" style="left:428px;top:22px;width:270px;height:380px;">
    <svg class="art" width="270" height="380" viewBox="0 0 270 380">
      <defs>
        <linearGradient id="lhBand2" x1="0" y1="0" x2="1" y2="1">
          <stop offset="0" stop-color="var(--brand-cyan)"/><stop offset="1" stop-color="var(--brand-navy)"/>
        </linearGradient>
      </defs>
      <path d="M80,0 H270 V58 C210,32 150,14 80,0Z" fill="url(#lhBand2)"/>
      <path d="M0,30 C90,22 180,40 270,66" fill="none" stroke="var(--brand-navy)" stroke-width="2"/>
      <path d="M20,350 H250" stroke="var(--brand-blue)" stroke-width="1"/>
    </svg>
    <div class="wordmark" style="left:10px;top:10px;font-size:9px;"><span class="dot" style="width:9px;height:9px;"></span>Tessel Brook</div>
    <div class="tagline" style="left:23px;top:24px;">an Energy Broker</div>
    <div class="watermark" role="img" aria-label="Faint enlarged brand emblem" style="left:50px;top:90px;width:170px;height:230px;"></div>
    <div class="contact dark" style="left:0;width:270px;top:355px;">47 Ambervale Court, Lakewood, NJ 09314 · (555) 014-TESS (8377)<br>www.tesselbrook.com</div>
  </section>
  <div class="item-label" style="left:428px;top:408px;width:270px;">Letterhead Option 2</div>

  <!-- Envelope back, black -->
  <section class="sheet envelope" style="left:864px;top:24px;width:300px;height:90px;background:var(--night);">
    <svg class="art" width="300" height="90" viewBox="0 0 300 90">
      <path d="M0,0 L150,52 L300,0" fill="none" stroke="#2b2d30" stroke-width="1"/>
    </svg>
    <div class="wordmark light" style="left:118px;top:20px;font-size:7px;"><span class="dot" style="width:7px;height:7px;"></span>Tessel Brook</div>
  </section>

  <!-- Envelope back, blue flap -->
  <section class="sheet envelope" style="left:864px;top:125px;width:300px;height:90px;">
    <svg class="art" width="300" height="90" viewBox="0 0 300 90">
      <defs>
        <linearGradient id="flap" x1="0" y1="0" x2="0" y2="1">
          <stop offset="0" stop-color="var(--brand-cyan)"/><stop offset="1" stop-color="var(--brand-blue)"/>
        </linearGradient>
      </defs>
      <path d="M0,0 H300 L150,55Z" fill="url(#flap)"/>
      <path d="M0,90 L130,40 M300,90 L170,40" stroke="#e3e7ea" stroke-width="1"/>
    </svg>
    <div class="wordmark light" style="left:118px;top:14px;font-size:7px;"><span class="dot" style="width:7px;height:7px;background:var(--paper);"></span>Tessel Brook</div>
  </section>

  <!-- Envelope back, plain -->
  <section class="sheet envelope" style="left:864px;top:223px;width:300px;height:90px;">
    <svg class="art" width="300" height="90" viewBox="0 0 300 90">
      <path d="M0,0 L150,50 L300,0 M0,90 L130,42 M300,90 L170,42" fill="none" stroke="#dfe3e6" stroke-width="1"/>
    </svg>
  </section>

  <!-- Envelope front -->
  <section class="sheet envelope" style="left:864px;top:322px;width:300px;height:86px;">
    <svg class="art" width="300" height="86" viewBox="0 0 300 86">
      <defs>
        <linearGradient id="envBand" x1="0" y1="0" x2="1" y2="1">
          <stop offset="0" stop-color="var(--brand-cyan)"/><stop offset="1" stop-color="var(--brand-navy)"/>
        </linearGradient>
      </defs>
      <path d="M120,0 H300 V30 C240,14 180,5 120,0Z" fill="url(#envBand)"/>
      <path d="M0,74 C100,64 200,70 300,56 V86 H0Z" fill="url(#envBand)"/>
    </svg>
    <div class="wordmark" style="left:8px;top:7px;font-size:7px;"><span class="dot" style="width:7px;height:7px;"></span>Tessel Brook</div>
    <div class="tagline" style="left:18px;top:18px;line-height:1.4;">47 Ambervale Court<br>Lakewood, NJ 09314</div>
  </section>
  <div class="item-label" style="left:864px;top:413px;width:300px;">Envelope Front &amp; Back</div>
</body>
</html>
```